Business Card Design and Logo Needed

I need Business Cards and a Logo for my website and public speaking business which can be found at: www.corvina-lett.example

I'm looking for creative and unique ideas. Some business cards I've found online that I like can be found at:
http://gigbarrow.example/general/18-smokin-hot-business-card-designs/

and at

http://www.plumquarry.example/2009/04/50-creative-business-cards-of-50-graphic-designers/

```html
<!DOCTYPE html>
<html lang="en">
<head>
<meta charset="utf-8">
<title>Corvina Lett – Business Card</title>
<link rel="stylesheet" href="https://fonts.googleapis.com/css2?family=Comfortaa:wght@700&family=Nanum+Pen+Script&display=swap">
<style>
  :root {
    --page-bg: #000000;
    --card-bg: #5f5650;
    --title-ink: #f3cf98;
    --contact-ink: #f7a35c;
    --mark-top: #ffd98a;
    --mark-bottom: #ff7a45;
  }
  html, body {
    margin: 0;
    padding: 0;
    width: 1012px;
    height: 1200px;
    overflow: hidden;
    background: var(--page-bg);
  }
  .canvas {
    position: relative;
    width: 1012px;
    height: 1200px;
    background: var(--page-bg);
  }
  .card-shape,
  .roles {
    position: absolute;
    left: 0;
    top: 0;
  }
  .roles text {
    font-family: "Nanum Pen Script", cursive;
    font-size: 66px;
    fill: var(--title-ink);
  }
  .contact {
    position: absolute;
    right: 217px;
    top: 585px;
    margin: 0;
    text-align: right;
    font-family: "Comfortaa", sans-serif;
    font-weight: 700;
    font-size: 31px;
    line-height: 50px;
    color: var(--contact-ink);
    font-style: normal;
  }
  .contact span { display: block; }
  .brand {
    position: absolute;
    left: 213px;
    width: 605px;
    top: 828px;
    display: flex;
    flex-direction: column;
    align-items: center;
    gap: 14px;
  }
  .brand-dot {
    width: 206px;
    height: 206px;
    border-radius: 50%;
    background: linear-gradient(180deg, var(--mark-top), var(--mark-bottom));
  }
  .brand-name {
    font-family: "Comfortaa", sans-serif;
    font-weight: 700;
    font-size: 30px;
    line-height: 40px;
    color: var(--contact-ink);
  }
</style>
</head>
<body>
<main class="canvas">
  <svg class="card-shape" width="1012" height="1200" viewBox="0 0 1012 1200" aria-hidden="true">
    <path fill="var(--card-bg)" d="M253 150 L700 150 C712 195 760 240 818 243 L818 1068 Q818 1118 768 1118 L253 1118 Q213 1118 213 1078 L213 190 Q213 150 253 150 Z"/>
  </svg>

  <svg class="roles" width="1012" height="1200" viewBox="0 0 1012 1200" role="list" aria-label="Roles">
    <text role="listitem" x="238" y="358" textLength="470" lengthAdjust="spacingAndGlyphs">Motivational Speaker</text>
    <text role="listitem" x="238" y="443" textLength="336" lengthAdjust="spacingAndGlyphs">Philanthropist</text>
    <text role="listitem" x="238" y="526" textLength="162" lengthAdjust="spacingAndGlyphs">Author</text>
  </svg>

  <address class="contact">
    <span class="contact-phone">mob : 0123 456780</span>
    <span class="contact-web">www.corvina-lett.example</span>
    <span class="contact-email">corvina@lettmail.example</span>
  </address>

  <div class="brand">
    <div class="brand-dot"></div>
    <div class="brand-name">Corvina Lett</div>
  </div>
</main>
</body>
</html>
```